We need a new website design for our company Brindle Forks (https://www.brindleforks.com/). We DO NOT WANT A BORING STANDARD SITE. This site has to be different, and has to POP!

Logo Files: https://files.examplecloud.net/folders/a7Kq3Lm9Zx2Tp8Rw4Vn6Yb1Hc5Jd0Fs

Website Photos here: https://files.examplecloud.net/folders/b3Wm8Qx_T2ngVr7Lp4Ks9Hd6Zc1Ya0Ej

Websites we like:
https://morvenite.sitebloom.io/
http://crunova.com/

We will need the site building Wordpress/Woocommerce and also help with interior pages & installation plug-ins -- see further attachments.

Information about the company:
1. PURPOSE: Why do we exist?
We believe that food is the root source to healthy living.
2. VISION: What future do we want to help create?
A world of healthy and happy people.
3. MISSION: What are we here to do?
Empower every person to utilize food as a means of living a healthy life.

Value Proposition:
Brindle Forks develops new food based on the latest science to provide the human body with the proper nutrients for optimal health. Our research based foods target the key health functions that support healthy aging and active lifestyles. Since 2002, we have been innovating and designing our meals to meet the needs for healthy aging to active lifestyles. To help people perform their best, today & in the future.

Objective:
This is a nationwide issue and it's coming to the surface. Food affects people in a number of different ways. Our objective is to create an approachable and sustainable solution that can assist people with a number of ailments. The end result for all of them is feeling a feeling they haven't felt in quite some time. Feeling a refreshed you. Like water for fish, food for humans. Keep it clean and simple so you can focus on enjoying your life.

PHRASES/TAGLINES:
Empowerment Through Food
Real Food, Real Results
Nutrition Made Simple
Not Just Meal Prep, Food Science
A healthier you, delivered to your door
Increase your health and wellness baseline.
Discover the potential of healthier eating
Become the best version of you
It’s incredible what proper nutrition feels like
Taste & feel the difference. Your future self will thank you.
A healthier you is just a meal away
Life Changing results
Overwhelmed with being healthy, stops here.
Designed by doctors, approved by humans
Results Driven Healthy Eating, Delivered to you.
Become the person you deserve to be.
Enjoy the process of becoming a better you

Value Propositions:
We Educate & Empower People Through Food to Live Their Best Life
Sustainable health through proper nutrition… that’s enjoyable too.

Key Statements:
We provide satisfying meals that are nutrient dense & deliver results.
Our meals provide an easy way to enjoy an anti-inflammatory diet that's as satisfying as it is healthy.
Health, fat loss & feeling good through chef-prepared, nutrient-dense, satisfying meals delivered to your door.

PLEASE REVIEW THE ATTACHMENTS.

Industry/Entity Type

See Description & Attachments

Coding

Coded - Design and coding required

Number of Pages Required

5+ page

Font styles to use
Other font styles liked:
• See Description & Attachments

Colors
0094D4
00A9DD
6FCCEA
C7EBF8
E9F6FB
00AB8E
00BBA5
67D7C9
C6EFE9
E9F9F6

Requirements
Must have
Nice to have
Should not have

```html
<!DOCTYPE html>
<html lang="en">
<head>
<meta charset="utf-8">
<title>Brindle Forks — A healthier you, delivered to your door</title>
<link href="https://fonts.googleapis.com/css2?family=Josefin+Sans:wght@400;600;700&family=Montserrat:wght@300;400;500&display=swap" rel="stylesheet">
<style>
:root{
  --green:#0c5a47;
  --ink:#1b1b1b;
  --text:#3c3c3c;
  --white:#ffffff;
  --footer:#0b0b0b;
}
*{box-sizing:border-box;margin:0;padding:0}
html,body{width:1200px;height:3710px;overflow:hidden}
body{position:relative;background:var(--white);font-family:"Montserrat",sans-serif;color:var(--text)}
.abs{position:absolute}
.display{font-family:"Josefin Sans",sans-serif;font-weight:700;color:var(--ink)}
.accent{color:var(--green)}
.btn{position:absolute;display:flex;align-items:center;justify-content:center;border-radius:30px;font-family:"Josefin Sans",sans-serif;font-weight:600;font-size:19px}
.btn-green{background:var(--green);color:var(--white);box-shadow:0 4px 8px rgba(0,0,0,.18)}
.btn-white{background:var(--white);color:var(--green)}

/* nav */
.site-nav{position:absolute;top:0;left:0;width:1200px;height:92px}
.brand{position:absolute;left:62px;top:36px;font-family:"Josefin Sans",sans-serif;font-weight:700;font-size:24px;color:var(--green);white-space:nowrap}
.nav-link{position:absolute;top:38px;font-family:"Josefin Sans",sans-serif;font-weight:600;font-size:17px;color:var(--ink)}
.nav-link.active{color:var(--green);text-decoration:underline;text-underline-offset:4px}
.cart-count{display:inline-block;width:16px;height:16px;border-radius:50%;background:#9bb7a9;color:#fff;font-size:10px;text-align:center;line-height:17px;margin-left:6px}
.nav-phone{left:948px;top:27px;width:183px;height:41px;font-size:16px;justify-content:flex-start;padding-left:8px;gap:12px;border:2px solid #d6e6df}
.phone-dot{width:28px;height:28px;border-radius:50%;background:#fff;display:flex;align-items:center;justify-content:center}

/* hero */
.hero-panel{position:absolute;left:0;top:92px;width:600px;height:570px;background:var(--green)}
.hero-photo{position:absolute;left:600px;top:92px;width:600px;height:574px;background:linear-gradient(135deg,#dfe8d8 0%,#e9c6bd 45%,#d9a89c 70%,#b9cfa6 100%)}
.hero-title{position:absolute;left:111px;top:208px;width:480px;font-size:58px;line-height:61px;color:var(--white)}
.hero-copy{position:absolute;left:111px;top:400px;width:440px;font-size:14.5px;line-height:28px;color:#e6f0ec;font-weight:300}
.hero-btn{left:111px;top:491px;width:128px;height:49px}

/* awards */
.section-title{position:absolute;left:0;width:1200px;text-align:center;font-size:36px}
.stat{position:absolute;top:812px;width:230px;text-align:center}
.stat svg{width:96px;height:96px;display:block;margin:0 auto}
.stat-num{font-family:"Josefin Sans",sans-serif;font-weight:700;font-size:30px;color:var(--ink);margin-top:16px}
.stat-label{font-family:"Josefin Sans",sans-serif;font-size:18px;line-height:27px;color:var(--ink);margin-top:8px}

/* menus */
.menus-bg{position:absolute;left:0;top:1073px;width:1200px;height:802px;background:radial-gradient(circle at 50% 50%,#9a9a98 0%,#6f6f6d 55%,#4a4a48 100%)}
.menus-card{position:absolute;left:137px;top:1145px;width:925px;height:661px;background:var(--white)}
.menus-title{position:absolute;left:44px;top:70px;font-size:34px}
.menus-intro{position:absolute;left:278px;top:27px;font-size:14px}
.menus-btn{left:279px;top:53px;width:198px;height:52px}
.dish{position:absolute;width:279px}
.dish-photo{width:279px;height:205px;border-radius:14px;position:relative}
.dish-name{position:absolute;left:20px;right:20px;bottom:0;height:28px;background:#fff;border-radius:14px 14px 0 0;text-align:center;font-size:14px;font-weight:500;color:var(--ink);line-height:34px}
.dish-meta{text-align:center;font-size:12.5px;color:var(--green);margin-top:8px}

/* who */
.who-photo{position:absolute;left:96px;top:1925px;width:468px;height:405px;border-radius:50%;background:radial-gradient(circle at 50% 50%,#e9d2b5 0%,#c98f5c 35%,#7aa968 60%,#e7efe4 78%,#ffffff 100%)}
.who-title{position:absolute;left:618px;top:1970px;font-size:35px}
.who-copy{position:absolute;left:618px;width:455px;font-size:14px;line-height:28px;font-weight:400}
.who-feature{position:absolute;font-size:14.5px;font-weight:500;color:var(--ink);display:flex;align-items:center;gap:10px}
.who-feature svg{width:22px;height:22px}
.who-btn{left:618px;top:2275px;width:130px;height:50px}

/* band */
.band{position:absolute;left:0;top:2386px;width:1200px;height:574px;background:radial-gradient(circle at 50% 45%,#2a2a27 0%,#1a1917 55%,#0d0c0b 100%)}
.band-title{position:absolute;left:0;top:70px;width:1200px;text-align:center;font-size:36px;line-height:41px;color:var(--white)}
.band-copy{position:absolute;left:190px;width:820px;text-align:center;font-size:14.5px;line-height:31px;color:#f0f0f0}
.band-btn1{left:315px;top:439px;width:292px;height:50px}
.band-btn2{left:632px;top:439px;width:257px;height:50px;justify-content:flex-start;padding-left:8px;gap:12px;font-family:"Montserrat",sans-serif;font-weight:500;font-size:16px}
.band-btn2 .phone-dot{background:var(--green)}

/* newsletter */
.news-copy{position:absolute;left:240px;top:3088px;width:720px;text-align:center;font-size:14px;line-height:28px}
.news-form{position:absolute;left:177px;top:3155px;width:845px;height:73px;border-radius:37px;background:#fff;box-shadow:0 2px 14px rgba(0,0,0,.14);overflow:hidden}
.news-field{position:absolute;left:25px;top:27px;font-family:"Josefin Sans",sans-serif;font-size:15px;color:#777}
.news-submit{position:absolute;right:0;top:0;width:194px;height:73px;background:var(--green);color:#fff;display:flex;align-items:center;justify-content:center;font-family:"Josefin Sans",sans-serif;font-weight:600;font-size:24px}

/* footer */
.footer-wave{position:absolute;left:0;top:3262px;width:1200px;height:60px}
.footer{position:absolute;left:0;top:3320px;width:1200px;height:390px;background:var(--footer);color:#e5e5e5}
.foot-col{position:absolute;top:52px}
.foot-head{font-family:"Josefin Sans",sans-serif;font-weight:700;font-size:20px;color:#fff;margin-bottom:22px}
.foot-link{font-size:14px;line-height:38px;font-weight:300}
.foot-link::before{content:"»";margin-right:10px}
.contact-row{width:196px;border-bottom:1px solid #8a8a8a;padding:10px 0 14px;font-size:14px;font-weight:300;display:flex;gap:10px;line-height:26px}
.contact-row svg{width:16px;height:16px;margin-top:5px;flex:none}
.foot-brand{position:absolute;left:800px;top:150px;width:295px;text-align:center;font-family:"Josefin Sans",sans-serif;font-weight:700;font-size:38px;line-height:44px;color:#fff;white-space:nowrap}
.foot-rule{position:absolute;left:111px;top:316px;width:978px;height:1px;background:#8a8a8a}
.copyright{position:absolute;left:111px;top:355px;font-size:14px;font-weight:300}
.social{position:absolute;top:352px;width:20px;height:20px;border-radius:50%;background:var(--green)}
</style>
</head>
<body>

<svg width="0" height="0" style="position:absolute">
  <defs>
    <symbol id="phone" viewBox="0 0 24 24">
      <path d="M6.6 10.8a15.1 15.1 0 0 0 6.6 6.6l2.2-2.2a1 1 0 0 1 1-.25 11.4 11.4 0 0 0 3.6.57 1 1 0 0 1 1 1V20a1 1 0 0 1-1 1A17 17 0 0 1 3 4a1 1 0 0 1 1-1h3.5a1 1 0 0 1 1 1c0 1.25.2 2.45.57 3.57a1 1 0 0 1-.25 1z"/>
    </symbol>
  </defs>
</svg>

<!-- navigation -->
<header class="site-nav">
  <div class="brand">Brindle Forks</div>
  <span class="nav-link active" style="left:319px">Home</span>
  <span class="nav-link" style="left:420px">Menu ▾</span>
  <span class="nav-link" style="left:518px">How Its Work</span>
  <span class="nav-link" style="left:680px">Shop ▾</span>
  <span class="nav-link" style="left:820px">🛒︎ Cart<span class="cart-count">0</span></span>
  <div class="btn btn-green nav-phone"><span class="phone-dot"><svg width="15" height="15" fill="#0c5a47"><use href="#phone"/></svg></span>+1 555 014 2290</div>
</header>

<!-- hero -->
<section>
  <div class="hero-panel"></div>
  <div class="hero-photo" role="img" aria-label="Smiling woman eating a fresh salad with a fork"></div>
  <svg class="abs" style="left:0;top:630px" width="1200" height="50" viewBox="0 0 1200 50" preserveAspectRatio="none">
    <path d="M0 20 C200 40 400 10 600 28 C800 46 1000 8 1200 30 L1200 50 L0 50Z" fill="#fff"/>
  </svg>
  <svg class="abs" style="left:600px;top:84px" width="600" height="20" viewBox="0 0 600 20" preserveAspectRatio="none">
    <path d="M0 14 C150 2 350 18 600 4 L600 0 L0 0Z" fill="#fff"/>
  </svg>
  <h1 class="display hero-title">A healthier you, delivered to your door.</h1>
  <p class="hero-copy">Brindle Forks develops new food based on the latest science to provide the human body with the proper nutrients for optimal health.</p>
  <div class="btn btn-white hero-btn">Shop Now</div>
</section>

<!-- awards -->
<section>
  <h2 class="display section-title" style="top:742px">Award <span class="accent">Winning</span> Meals</h2>

  <div class="stat" style="left:62px">
    <svg viewBox="0 0 96 96" fill="none" stroke="#0c5a47" stroke-width="3">
      <circle cx="48" cy="50" r="9"/><path d="M32 80c0-10 7-16 16-16s16 6 16 16z"/>
      <circle cx="24" cy="58" r="7"/><path d="M10 82c0-8 6-12 14-12"/>
      <circle cx="72" cy="58" r="7"/><path d="M86 82c0-8-6-12-14-12"/>
      <path d="M48 8l3 7 7 .5-5.5 4.5 2 7L48 23l-6.5 4 2-7L38 15.5l7-.5z"/>
      <path d="M22 26l2 4 4 .5-3 3 1 4-4-2-4 2 1-4-3-3 4-.5z"/>
      <path d="M74 26l2 4 4 .5-3 3 1 4-4-2-4 2 1-4-3-3 4-.5z"/>
    </svg>
    <div class="stat-num">150K</div><div class="stat-label">Happy Clients</div>
  </div>
  <div class="stat" style="left:340px">
    <svg viewBox="0 0 96 96" fill="none" stroke="#0c5a47" stroke-width="3">
      <path d="M14 54a34 34 0 0 1 68 0z"/><circle cx="48" cy="17" r="3"/>
      <path d="M10 60h76"/><path d="M22 76c8-6 16-10 26-8l14 2c4 1 4 6 0 6H48"/>
      <path d="M10 80l12-6"/><path d="M14 12l2 4 4 1-4 1-2 4-2-4-4-1 4-1z"/>
    </svg>
    <div class="stat-num">500K</div><div class="stat-label">Meals Served Nation<br>Wide</div>
  </div>
  <div class="stat" style="left:618px">
    <svg viewBox="0 0 96 96" fill="none" stroke="#0c5a47" stroke-width="3">
      <path d="M34 22c0-8 6-12 12-12s12 4 12 12z"/><path d="M34 22h24v6H34z"/>
      <circle cx="46" cy="38" r="9"/><path d="M26 88V62c0-8 8-12 20-12s20 4 20 12v26"/>
      <path d="M46 50v38"/><path d="M14 54v24"/><path d="M10 50h8"/>
      <path d="M62 70h26v14H62z"/><path d="M70 62c0-4 4-4 4-8M80 62c0-4 4-4 4-8"/>
    </svg>
    <div class="stat-num">35+</div><div class="stat-label">Chef Prepared Meals</div>
  </div>
  <div class="stat" style="left:895px">
    <svg viewBox="0 0 96 96" fill="none" stroke="#0c5a47" stroke-width="3">
      <circle cx="48" cy="38" r="28"/><circle cx="48" cy="38" r="20"/>
      <path d="M48 26l4 8 8 1-6 6 2 8-8-4-8 4 2-8-6-6 8-1z"/>
      <path d="M30 60L20 86l12-4 6 10 10-26"/><path d="M66 60l10 26-12-4-6 10-10-26"/>
    </svg>
    <div class="stat-num">215</div><div class="stat-label">Awards Winning</div>
  </div>
</section>

<!-- menus -->
<section>
  <div class="menus-bg" role="img" aria-label="Kitchen table with tomatoes, herbs, spices, lime and onion"></div>
  <div class="menus-card">
    <h2 class="display menus-title">Our <span class="accent">Menus</span></h2>
    <p class="menus-intro">Chef Prepared Meals... Delivered FreshWeight Loss. Health Issues. We've Got You.</p>
    <div class="btn btn-green menus-btn">View Plan &amp; Menu</div>

    <div class="dish" style="left:25px;top:128px">
      <div class="dish-photo" role="img" aria-label="Roast chicken with potatoes and lemon" style="background:linear-gradient(135deg,#5a3a1c,#b88238,#3b2a18)"><div class="dish-name">Chicken</div></div>
      <div class="dish-meta">580 | Gulten Free | Single Serve</div>
    </div>
    <div class="dish" style="left:324px;top:128px">
      <div class="dish-photo" role="img" aria-label="Grilled beef steak with vegetables in a pan" style="background:linear-gradient(135deg,#1e1e1e,#5a3b2c,#2b2b2b)"><div class="dish-name">Beef</div></div>
      <div class="dish-meta">490 | Lactose Free | Single Serve</div>
    </div>
    <div class="dish" style="left:622px;top:128px">
      <div class="dish-photo" role="img" aria-label="Avocado toast with egg on a white plate" style="background:linear-gradient(135deg,#dfeee6,#f4f2ea,#cfe3d6)"><div class="dish-name">Breakfast</div></div>
      <div class="dish-meta">599 | Lactose Free | Single Serve</div>
    </div>
    <div class="dish" style="left:25px;top:395px">
      <div class="dish-photo" role="img" aria-label="Fresh salad with berries and greens" style="background:linear-gradient(135deg,#eef0f0,#c9d8b8,#e5e7e6)"><div class="dish-name">Salads</div></div>
      <div class="dish-meta">580 | Gulten Free | Single Serve</div>
    </div>
    <div class="dish" style="left:324px;top:395px">
      <div class="dish-photo" role="img" aria-label="Grilled salmon with asparagus and lemon" style="background:linear-gradient(135deg,#2a2a2a,#c06a3c,#333)"><div class="dish-name">Seafood</div></div>
      <div class="dish-meta">510 | Lactose Free | Single Serve</div>
    </div>
    <div class="dish" style="left:622px;top:395px">
      <div class="dish-photo" role="img" aria-label="Chicken noodle soup in a white bowl" style="background:linear-gradient(135deg,#a48a7c,#efc45a,#8f7467)"><div class="dish-name">Soup</div></div>
      <div class="dish-meta">599 | Lactose Free | Single Serve</div>
    </div>
  </div>
</section>

<!-- who -->
<section>
  <div class="who-photo" role="img" aria-label="Grilled chicken breast with salad vegetables on a plate"></div>
  <h2 class="display who-title">Who is <span class="accent">Brindle Forks</span> For?</h2>
  <p class="who-copy" style="top:2008px">More than just a meal plan, we provide a sustainable diet &amp; nutritional support that empowers you to live your best life, no matter your health goals.</p>
  <p class="who-copy" style="top:2116px">Weight Loss. Health Issues. Improved Performance. We've Got You.</p>
  <div class="who-feature" style="left:618px;top:2188px"><svg viewBox="0 0 24 24" fill="none" stroke="#0c5a47" stroke-width="1.8"><path d="M12 20s-8-5-8-11a4 4 0 0 1 8-1 4 4 0 0 1 8 1c0 6-8 11-8 11z"/><path d="M6 11h3l2-3 2 5 2-2h3"/></svg>General Health</div>
  <div class="who-feature" style="left:842px;top:2188px"><svg viewBox="0 0 24 24" fill="none" stroke="#0c5a47" stroke-width="1.8"><path d="M3 21h18M5 21V12M9 21V9M13 21V11M17 21V6M4 8l5-4 4 3 6-5"/></svg>Business Individuals</div>
  <div class="who-feature" style="left:618px;top:2223px"><svg viewBox="0 0 24 24" fill="none" stroke="#0c5a47" stroke-width="1.8"><rect x="3" y="3" width="12" height="18" rx="1"/><path d="M6 8h6M6 12h6M15 14h6v7h-6z"/></svg>Fitness Enthusiasts</div>
  <div class="who-feature" style="left:842px;top:2223px"><svg viewBox="0 0 24 24" fill="none" stroke="#0c5a47" stroke-width="1.8"><circle cx="12" cy="8" r="3"/><path d="M6 20c0-4 3-6 6-6s6 2 6 6"/><circle cx="4" cy="12" r="2"/><circle cx="20" cy="12" r="2"/></svg>Professional Athletes</div>
  <div class="btn btn-green who-btn">Read More</div>
</section>

<!-- performance band -->
<section class="band" role="img" aria-label="Dark food backdrop with herbs and vegetables">
  <h2 class="display band-title">Weight Loss. Health Issues. Improved Performance.<br>We've Got You.</h2>
  <p class="band-copy" style="top:157px">More than just a meal plan, we provide a sustainable diet &amp; nutritional support that empowers you to live your best life, no matter your health goals.Brindle Forks develops new food based on the latest science to provide the human body with the proper nutrients for optimal health. Our research based foods target the key health functions that support healthy aging and active lifestyles. Since 2002, we have been innovating and designing our meals to meet the needs for healthy aging to active lifestyles.</p>
  <p class="band-copy" style="top:343px">To help people perform their best, today &amp; in the future.More than just a meal plan, we provide a sustainable diet &amp; nutritional support that empowers you to live your best life, no matter your health goals.</p>
  <div class="btn btn-green band-btn1">Fresh Meals Delivered Weekly</div>
  <div class="btn btn-white band-btn2"><span class="phone-dot"><svg width="15" height="15" fill="#fff"><use href="#phone"/></svg></span>Call : +1 555 014 2290</div>
</section>

<!-- newsletter -->
<section>
  <h2 class="display section-title" style="top:3040px">Join <span class="accent">Our</span> Newsletter</h2>
  <p class="news-copy">Eating properly is no longer difficult. We've handcrafted delicious meals that are results driven, so all you need to do is, enjoy.</p>
  <div class="news-form">
    <span class="news-field">Enter The Email</span>
    <span class="news-submit">Subscribe</span>
  </div>
</section>

<!-- footer -->
<svg class="footer-wave" viewBox="0 0 1200 60" preserveAspectRatio="none">
  <path d="M0 30 C150 10 300 40 450 22 C600 6 750 30 900 18 C1030 8 1120 24 1200 14 L1200 60 L0 60Z" fill="#0b0b0b"/>
</svg>
<footer class="footer">
  <div class="foot-col" style="left:111px">
    <div class="foot-head">Quick Links</div>
    <div class="foot-link">Home</div><div class="foot-link">About</div><div class="foot-link">Menu</div><div class="foot-link">Blog</div><div class="foot-link">Who Is Brindle Forks</div>
  </div>
  <div class="foot-col" style="left:323px">
    <div class="foot-head">Other Links</div>
    <div class="foot-link">FAQ</div><div class="foot-link">Privacy</div><div class="foot-link">Condition</div><div class="foot-link">Terms</div><div class="foot-link">Contact Us</div>
  </div>
  <div class="foot-col" style="left:535px">
    <div class="foot-head" style="margin-bottom:8px">Contact Us</div>
    <div class="contact-row"><svg viewBox="0 0 16 16" fill="none" stroke="#ccc"><path d="M8 15s5-5 5-9A5 5 0 0 0 3 6c0 4 5 9 5 9z"/><circle cx="8" cy="6" r="2"/></svg><span>Brindle Forks<br>United States</span></div>
    <div class="contact-row"><svg viewBox="0 0 16 16" fill="none" stroke="#ccc"><rect x="1.5" y="3.5" width="13" height="9"/><path d="M1.5 3.5l6.5 5 6.5-5"/></svg><span>info@brindleforks.com</span></div>
    <div class="contact-row"><svg viewBox="0 0 24 24" fill="#ccc"><use href="#phone"/></svg><span>+1 555 014 2290</span></div>
  </div>
  <div class="foot-brand">Brindle Forks</div>
  <div class="foot-rule"></div>
  <div class="copyright">Copyrights@2022.Brindle Forks.All Rights Reserved</div>
  <span class="social" style="left:950px"></span>
  <span class="social" style="left:990px"></span>
  <span class="social" style="left:1030px"></span>
  <span class="social" style="left:1070px"></span>
</footer>

</body>
</html>
```